Wed site for biomedical device startup

We need a generic website for a medical device startup. I will provide examples below of websites from other companies that can serve as models for what we are looking for. The startup is for a device that can non invasively measure blood flow in the brain using light. The application is to detect the type of stroke someone is having before they get to the hospital so treatment can be started right away. This saves patients upto hours of delayed treatment. Patients will be able to recover from stroke much better and faster as a result. I have attached an AI generated illustration of what the device will ultimately look like for reference.

https://www.372clinicaltech.com
https://vextalune.com

Target Market(s)

Biomedical, medical device, investors of biomedical device startups

Industry/Entity Type

Biomedical

Coding

Coded - Design and coding required

Number of Pages Required

4 page

Requirements
Must have
• same section and section headings as example websites listed above
Nice to have
• similar to example websites listed above. Prefer a darker website over a lighter one. Perhaps dark blues to go with logo colors. A moving background image element at top of landing page could be cool. Something indicative of heartbeat, or neurons, or blood flow.

```html
<!DOCTYPE html>
<html lang="en">
<head>
<meta charset="utf-8">
<title>NEVRA — Innovating Health with Precision Science</title>
<link rel="stylesheet" href="https://fonts.googleapis.com/css2?family=Montserrat:wght@400;500;600;700&display=swap">
<style>
:root{
  --bg-deep:#03021f;
  --bg-navy:#0b0a3a;
  --card:#23252c;
  --white:#ffffff;
  --muted:#c9c9d6;
  --grey:#9a9aa8;
  --cyan:#1ec8e6;
  --violet:#7b3fe4;
  --line:#5a5ee0;
}
*{box-sizing:border-box;margin:0;padding:0}
html,body{width:1200px;height:2803px;overflow:hidden}
body{background:var(--bg-deep);color:var(--white);font-family:"Montserrat",sans-serif;position:relative}
.brand{display:flex;align-items:center;gap:12px;font-weight:500;color:var(--white)}
.brand-dot{width:60px;height:60px;border-radius:50%;background:var(--violet)}
.brand-name{font-size:46px;letter-spacing:2px;white-space:nowrap}

/* header */
.site-header{position:absolute;left:0;top:0;width:1200px;height:86px;background:var(--bg-deep)}
.site-header .brand{position:absolute;left:112px;top:12px}
.main-nav{position:absolute;left:589px;top:32px;display:flex;gap:46px;font-size:16px;white-space:nowrap}
.main-nav a{color:var(--white);text-decoration:none}
.main-nav .active{font-weight:600;position:relative}
.main-nav .active::before{content:"";position:absolute;left:0;right:0;top:-32px;height:5px;background:linear-gradient(90deg,var(--cyan),var(--violet))}

/* hero */
.hero{position:absolute;left:0;top:86px;width:1200px;height:514px;
  background:radial-gradient(ellipse at 30% 30%,#3a3fb0 0%,#22258f 40%,#171a6a 100%)}
.hero-panel{position:absolute;left:150px;top:108px;width:900px;height:298px;background:rgba(10,10,40,.55);text-align:center}
.hero-title{font-size:38px;font-weight:700;margin-top:40px;white-space:nowrap}
.hero-text{font-size:15.5px;line-height:26px;width:690px;margin:30px auto 0;font-weight:500}
.btn-gradient{display:inline-flex;align-items:center;gap:8px;background:linear-gradient(90deg,var(--cyan),var(--violet));color:var(--white);border-radius:5px;font-size:13px;font-weight:500;text-decoration:none}
.hero .btn-gradient{margin-top:22px;padding:9px 24px}
.hero-dots{position:absolute;left:565px;top:453px;display:flex;gap:9px;align-items:center}
.hero-dots span{width:11px;height:11px;border-radius:50%;background:var(--white)}
.hero-dots span.on{width:15px;height:15px;background:linear-gradient(90deg,var(--cyan),var(--violet))}

/* technology */
.tech{position:absolute;left:0;top:600px;width:1200px;height:724px;background:var(--bg-deep)}
.eyebrow{position:absolute;left:111px;top:84px;font-size:17px;font-weight:500}
.section-title{font-size:35px;font-weight:600;line-height:41px}
.tech .section-title{position:absolute;left:111px;top:116px}
.tech-sub{position:absolute;left:111px;top:210px;font-size:16px}
.arrow-btn{position:absolute;top:132px;width:50px;height:50px;border-radius:50%;border:2px solid var(--white);display:flex;align-items:center;justify-content:center}
.arrow-btn.prev{left:960px;border-color:#4a4a5c}
.arrow-btn.next{left:1035px}
.feature-card{position:absolute;top:283px;width:225px;height:353px;background:var(--card);border-radius:10px;padding:36px 12px 0 21px}
.feature-card.featured{background:var(--bg-deep);border:1.5px solid var(--white)}
.feature-card svg.icon{width:90px;height:72px}
.feature-card h3{font-size:17px;font-weight:600;margin-top:18px;white-space:nowrap;letter-spacing:-.2px}
.feature-card p{font-size:12px;line-height:21px;color:var(--muted);margin-top:18px;padding-right:6px}
.card-btn{position:absolute;left:18px;bottom:36px;width:189px;height:34px;border:1px solid #cfcfd8;border-radius:5px;display:flex;align-items:center;justify-content:center;gap:7px;font-size:13px;font-weight:500;color:var(--white);white-space:nowrap}
.featured .card-btn{border:none;background:linear-gradient(90deg,var(--cyan),var(--violet))}

/* about */
.about{position:absolute;left:0;top:1324px;width:1200px;height:690px;
  background:radial-gradient(ellipse at 70% 30%,#1d2190 0%,#12145a 45%,#0a0b3a 100%)}
.about .section-title{position:absolute;left:111px;top:85px}
.about-divider{position:absolute;left:540px;top:90px;width:3px;height:77px;background:var(--line)}
.about-lead{position:absolute;left:587px;top:80px;width:510px;font-size:15px;line-height:23px}
.about-sub{position:absolute;left:111px;top:162px;font-size:19px;font-weight:600}
.check-list{position:absolute;left:111px;top:210px;list-style:none;width:420px}
.check-list li{display:flex;gap:16px;font-size:13px;line-height:21px;margin-bottom:16px}
.check-list .tick{flex:none;width:24px;height:24px;border-radius:50%;background:linear-gradient(135deg,var(--cyan),var(--violet));display:flex;align-items:center;justify-content:center;margin-top:4px}
.about-body{position:absolute;left:111px;top:330px;width:420px;font-size:13px;line-height:21.5px}
.about-body p{margin-bottom:12px}
.about-photo{position:absolute;width:240px;height:329px;border:3px solid;border-image:linear-gradient(180deg,var(--cyan),var(--violet)) 1}
.photo-blood{left:583px;top:222px;background:linear-gradient(160deg,#f04a6a 0%,#c8102e 50%,#8a0a22 100%)}
.photo-heart{left:855px;top:280px;background:radial-gradient(circle at 50% 45%,#f0c8d0 0%,#4a8ad0 30%,#1a4a9a 70%,#0c2a6a 100%)}

/* team */
.team{position:absolute;left:0;top:2014px;width:1200px;height:546px;background:var(--bg-deep);text-align:center}
.team .section-title{position:absolute;left:0;width:1200px;top:80px}
.member{position:absolute;top:174px;width:208px}
.member .portrait{width:208px;height:208px;border-radius:50%;background:linear-gradient(180deg,#d8dde2 0%,#7aa6c8 100%)}
.member h4{font-size:22px;font-weight:500;margin-top:32px;white-space:nowrap}
.member span{display:block;font-size:15px;color:var(--grey);margin-top:6px}

/* footer */
.site-footer{position:absolute;left:0;top:2560px;width:1200px;height:243px;background:var(--bg-navy)}
.site-footer .brand{position:absolute;left:483px;top:44px}
.footer-nav{position:absolute;left:324px;top:143px;display:flex;gap:51px;font-size:18px;font-weight:500;white-space:nowrap}
.footer-nav a{color:var(--white);text-decoration:none}
.footer-rule{position:absolute;left:0;top:192px;width:1200px;height:1px;background:#2a2a5a}
.copyright{position:absolute;left:0;width:1200px;top:208px;text-align:center;font-size:13px}
</style>
</head>
<body>

<header class="site-header">
  <div class="brand"><span class="brand-dot"></span><span class="brand-name">NEVRA</span></div>
  <nav class="main-nav">
    <a class="active" href="#">Home</a><a href="#">About</a><a href="#">Technology</a><a href="#">Press</a><a href="#">Contact Us</a>
  </nav>
</header>

<section class="hero" role="img" aria-label="Background of glowing blue neuron network">
  <div class="hero-panel">
    <h1 class="hero-title">Innovating Health with Precision Science</h1>
    <p class="hero-text">Lorem ipsum dolor sit amet, consectetur adipiscing elit, sed do eiusmod tempor incididunt ut labore et dolore magna aliqua. Quis ipsum suspendisse ultrices gravida. Risus commodo viverra maecenas accumsan lacus vel facilisis.</p>
    <a class="btn-gradient" href="#">Learn More
      <svg width="12" height="12" viewBox="0 0 12 12"><path d="M1 6h9M6 2l4 4-4 4" stroke="#fff" stroke-width="1.6" fill="none"/></svg></a>
  </div>
  <div class="hero-dots"><span class="on"></span><span></span><span></span><span></span></div>
</section>

<section class="tech">
  <p class="eyebrow">ADVANCED TECHNOLOGY</p>
  <h2 class="section-title">Innovative Blood Loss<br>Monitoring</h2>
  <p class="tech-sub">Lorem ipsum dolor sit amet, consectetur adipiscing elit,</p>
  <div class="arrow-btn prev"><svg width="24" height="16" viewBox="0 0 24 16"><path d="M23 8H2M9 1 2 8l7 7" stroke="#4a4a5c" stroke-width="2.4" fill="none"/></svg></div>
  <div class="arrow-btn next"><svg width="24" height="16" viewBox="0 0 24 16"><path d="M1 8h21M15 1l7 7-7 7" stroke="#fff" stroke-width="2.4" fill="none"/></svg></div>

  <article class="feature-card" style="left:111px">
    <svg class="icon" viewBox="0 0 90 72" fill="none" stroke="#cfcfd8" stroke-width="2"><rect x="1" y="2" width="70" height="54" rx="6"/><path d="M10 30h16l4-8 5 14 5-10 3 4h18"/><path d="M26 66h20M32 56v10M40 56v10"/></svg>
    <h3>Portable Monitoring</h3>
    <p>Lorem ipsum dolor sit amet, consectetur adipiscing elit, sed do eiusmod</p>
    <div class="card-btn">Craft Your Strategy <svg width="12" height="12" viewBox="0 0 12 12"><path d="M1 6h9M6 2l4 4-4 4" stroke="#fff" stroke-width="1.6" fill="none"/></svg></div>
  </article>
  <article class="feature-card featured" style="left:362px">
    <svg class="icon" viewBox="0 0 90 72" fill="none" stroke-width="2"><rect x="1" y="2" width="70" height="52" rx="3" stroke="#1ec8e6"/><path d="M10 40l12-12 12 6 12-14 12 8" stroke="#1ec8e6"/><path d="M28 64h24M34 54v10M46 54v10" stroke="#7b3fe4"/><circle cx="75" cy="44" r="13" stroke="#7b3fe4" fill="#03021f"/><path d="M75 37v8h6" stroke="#7b3fe4"/></svg>
    <h3>Real-time Alerts</h3>
    <p>Lorem ipsum dolor sit amet, consectetur adipiscing elit, sed do eiusmod</p>
    <div class="card-btn">Craft Your Strategy <svg width="12" height="12" viewBox="0 0 12 12"><path d="M1 6h9M6 2l4 4-4 4" stroke="#fff" stroke-width="1.6" fill="none"/></svg></div>
  </article>
  <article class="feature-card" style="left:612px">
    <svg class="icon" viewBox="0 0 90 72" fill="none" stroke="#cfcfd8" stroke-width="2"><path d="M8 8h6V2h6v6h6v6h-6v6h-6v-6H8z"/><path d="M4 58l14-14c6-6 14-4 20-2l20 0c4 0 4 6 0 6H40"/><path d="M30 30c8-6 20-6 30 0s10 14 2 16"/></svg>
    <h3>Patient-Centered</h3>
    <p>Lorem ipsum dolor sit amet, consectetur adipiscing elit, sed do eiusmod</p>
    <div class="card-btn">Craft Your Strategy <svg width="12" height="12" viewBox="0 0 12 12"><path d="M1 6h9M6 2l4 4-4 4" stroke="#fff" stroke-width="1.6" fill="none"/></svg></div>
  </article>
  <article class="feature-card" style="left:863px">
    <svg class="icon" viewBox="0 0 90 72" fill="none" stroke="#cfcfd8" stroke-width="2"><path d="M36 68C20 56 4 44 4 30 4 20 12 14 20 14c7 0 12 4 16 9 4-5 9-9 16-9 8 0 16 6 16 16 0 14-16 26-32 38z"/><path d="M8 40h14l4-8 6 14 5-10h31"/><path d="M26 8c6-6 14-6 20 0M31 12c3-3 7-3 10 0"/></svg>
    <h3>Health Technologies</h3>
    <p>Lorem ipsum dolor sit amet, consectetur adipiscing elit, sed do eiusmod</p>
    <div class="card-btn">Craft Your Strategy <svg width="12" height="12" viewBox="0 0 12 12"><path d="M1 6h9M6 2l4 4-4 4" stroke="#fff" stroke-width="1.6" fill="none"/></svg></div>
  </article>
</section>

<section class="about">
  <h2 class="section-title">About NEVRA</h2>
  <div class="about-divider"></div>
  <p class="about-lead">Lorem ipsum dolor sit amet, consectetur adipiscing elit, sed do eiusmod tempor incididunt ut labore et dolore magna aliqua. Quis ipsum suspendisse ultrices gravida. Risus commodo viverra maecenas accumsan lacus vel facilisis.</p>
  <h3 class="about-sub">Lorem ipsum dolor sit amet:</h3>
  <ul class="check-list">
    <li><span class="tick"><svg width="12" height="10" viewBox="0 0 12 10"><path d="M1 5l3.5 3.5L11 1" stroke="#fff" stroke-width="2" fill="none"/></svg></span>Lorem ipsum dolor sit amet, consectetur adipiscing elit, sed do eiusmod tempor</li>
    <li><span class="tick"><svg width="12" height="10" viewBox="0 0 12 10"><path d="M1 5l3.5 3.5L11 1" stroke="#fff" stroke-width="2" fill="none"/></svg></span>Lorem ipsum dolor sit amet, consectetur adipiscing elit, sed do eiusmod tempor</li>
  </ul>
  <div class="about-body">
    <p>Lorem ipsum dolor sit amet, consectetur adipiscing elit, sed do eiusmod tempor incididunt ut labore et dolore magna aliqua. Quis ipsum suspendisse ultrices gravida. Risus commodo viverra maecenas accumsan lacus vel facilisis.</p>
    <p>Lorem ipsum dolor sit amet, consectetur adipiscing elit, sed do eiusmod tempor incididunt ut labore et dolore magna aliqua.</p>
    <p>Lorem ipsum dolor sit amet, consectetur adipiscing elit, sed do eiusmod tempor incididunt ut labore et dolore magna aliqua. Quis ipsum suspendisse ultrices gravida.</p>
  </div>
  <div class="about-photo photo-blood" role="img" aria-label="Close-up of red blood cells flowing in a vessel"></div>
  <div class="about-photo photo-heart" role="img" aria-label="Glowing digital heart with heartbeat line above an open hand"></div>
</section>

<section class="team">
  <h2 class="section-title">Our Team Member</h2>
  <div class="member" style="left:113px"><div class="portrait" role="img" aria-label="Portrait photo of a team member"></div><h4>Arlen Voss</h4><span>Co-Founder</span></div>
  <div class="member" style="left:370px"><div class="portrait" role="img" aria-label="Portrait photo of a team member"></div><h4>Tobin Marsh</h4><span>Co-Founder</span></div>
  <div class="member" style="left:626px"><div class="portrait" role="img" aria-label="Portrait photo of a team member"></div><h4>Caspian Dorr</h4><span>Co-Founder</span></div>
  <div class="member" style="left:883px"><div class="portrait" role="img" aria-label="Portrait photo of a team member"></div><h4>Lena Quill</h4><span>Co-Founder</span></div>
</section>

<footer class="site-footer">
  <div class="brand"><span class="brand-dot"></span><span class="brand-name">NEVRA</span></div>
  <nav class="footer-nav"><a href="#">Home</a><a href="#">About</a><a href="#">Technology</a><a href="#">Press</a><a href="#">Contact Us</a></nav>
  <div class="footer-rule"></div>
  <p class="copyright">© 2025 NEVRA. All rights reserved.</p>
</footer>

</body>
</html>
```